BuildLinkHub.com Full Stationery Design

Business Card will have all info on it. Letterhead will not have name, title or mobile number. Keep general feeling very clean, using colors from the logo as accents.
Name:Dale Marchetti
Title:President
Phone: 1-800-555-0142
Cell: 306-555-0187
email: dale@buildlinkhub.example
website: www.buildlinkhub.example
Address:
PO Box 947
Lakefield, MB
S0J2T0

Target Market(s)

Construction Business owners

Industry/Entity Type

Business

Contact Information for Business Card

Name:Dale Marchetti
Title:President
Phone: 1-800-555-0142
Cell: 306-555-0187
Address:
PO Box 947
Lakefield, MB
S0J2T0

Font styles to use
Sans Serif

Requirements
Must have
• Clean look
Should not have
• Images or cartoon type characters or tools

```html
<!DOCTYPE html>
<html lang="en">
<head>
<meta charset="utf-8">
<title>BuildLinkHub.com Letterhead</title>
<link href="https://fonts.googleapis.com/css2?family=Montserrat:wght@600&family=Open+Sans:wght@400&display=swap" rel="stylesheet">
<style>
  :root {
    --backdrop: #efe6e4;
    --paper: #ffffff;
    --brand-orange: #e8600f;
    --brand-orange-deep: #dc4a12;
    --brand-grey: #5b6470;
    --swoosh-grey: #d9d9da;
    --text-grey: #6a6f76;
  }
  html, body {
    margin: 0;
    width: 1200px;
    height: 784px;
    overflow: hidden;
    background: var(--backdrop);
  }
  .canvas {
    position: relative;
    width: 1200px;
    height: 784px;
  }
  .letterhead {
    position: absolute;
    left: 320px;
    top: 30px;
    width: 560px;
    height: 724px;
    background: var(--paper);
    box-shadow: 0 4px 18px rgba(120, 80, 70, 0.18);
    overflow: hidden;
  }
  .corner-bars {
    position: absolute;
    top: 0;
    display: flex;
    gap: 4px;
  }
  .corner-bars span { display: block; height: 5px; }
  .corner-bars .bar-orange { width: 26px; background: var(--brand-orange); }
  .corner-bars .bar-grey { width: 26px; background: var(--brand-grey); opacity: .6; }
  .corner-bars.left { left: 0; }
  .corner-bars.right { right: 0; }
  .brand {
    position: absolute;
    left: 40px;
    top: 34px;
    display: flex;
    align-items: center;
    gap: 10px;
  }
  .brand-square {
    width: 22px;
    height: 22px;
    background: var(--brand-orange);
  }
  .brand-name {
    font-family: "Montserrat", sans-serif;
    font-weight: 600;
    font-size: 20px;
    color: var(--brand-grey);
    letter-spacing: .2px;
  }
  .contact {
    position: absolute;
    right: 34px;
    top: 34px;
    margin: 0;
    padding: 0;
    list-style: none;
    font-family: "Open Sans", sans-serif;
    font-size: 8.5px;
    line-height: 14px;
    color: var(--text-grey);
  }
  .contact li { display: flex; align-items: center; gap: 6px; white-space: nowrap; }
  .contact svg { width: 9px; height: 9px; flex: none; }
  .footer-wave {
    position: absolute;
    left: 0;
    bottom: 0;
    width: 560px;
    height: 220px;
  }
</style>
</head>
<body>
<div class="canvas">
  <section class="letterhead">
    <div class="corner-bars left"><span class="bar-orange"></span><span class="bar-grey"></span></div>
    <div class="corner-bars right"><span class="bar-grey"></span><span class="bar-orange"></span></div>

    <div class="brand">
      <span class="brand-square"></span>
      <span class="brand-name">BuildLinkHub.com</span>
    </div>

    <ul class="contact">
      <li><svg viewBox="0 0 10 10"><circle cx="5" cy="5" r="5" fill="#e8600f"/><path d="M5 2.2a1.8 1.8 0 0 0-1.8 1.8C3.2 5.4 5 7.8 5 7.8S6.8 5.4 6.8 4A1.8 1.8 0 0 0 5 2.2z" fill="#fff"/></svg>PO Box 947, Lakefield, MB, S0J2T0</li>
      <li><svg viewBox="0 0 10 10"><circle cx="5" cy="5" r="5" fill="#e8600f"/><path d="M3.3 2.5l1 1.1-.5.8c.3.6.8 1.1 1.4 1.4l.8-.5 1.1 1-.6.9C5 7 3 5 3 3.1z" fill="#fff"/></svg>Phone: 1-800-555-0142</li>
      <li><svg viewBox="0 0 10 10"><circle cx="5" cy="5" r="5" fill="#e8600f"/><rect x="2.6" y="3.4" width="4.8" height="3.2" fill="#fff"/><path d="M2.6 3.4L5 5.3l2.4-1.9" fill="none" stroke="#e8600f" stroke-width=".6"/></svg>dale@buildlinkhub.example</li>
      <li><svg viewBox="0 0 10 10"><circle cx="5" cy="5" r="5" fill="#e8600f"/><circle cx="5" cy="5" r="2.4" fill="none" stroke="#fff" stroke-width=".7"/><path d="M2.6 5h4.8M5 2.6v4.8" stroke="#fff" stroke-width=".6"/></svg>www.buildlinkhub.example</li>
    </ul>

    <svg class="footer-wave" viewBox="0 0 560 220" preserveAspectRatio="none" aria-hidden="true">
      <defs>
        <linearGradient id="waveFill" x1="0" y1="0" x2="1" y2="0">
          <stop offset="0" stop-color="#dc4a12"/>
          <stop offset="1" stop-color="#ee6c0a"/>
        </linearGradient>
      </defs>
      <path d="M0 220 L0 20 C50 0 110 40 230 110 C350 180 470 200 560 220 Z" fill="url(#waveFill)"/>
      <path d="M0 34 C50 16 110 54 230 122 C350 188 470 206 560 222" fill="none" stroke="#fff" stroke-width="10"/>
      <path d="M0 42 C55 24 115 62 235 130 C355 196 470 210 560 226" fill="none" stroke="#d9d9da" stroke-width="6"/>
      <path d="M0 6 C45 -8 100 28 225 100" fill="none" stroke="#e8600f" stroke-width="3"/>
    </svg>
  </section>
</div>
</body>
</html>
```